Velmo Swinger site - new website, blogsite and merchandise point, connection to tradeva

We are a well established Swingers Club in the North east of UK and already have an existing site. www.velmo-example.co.uk, BUT we have changed our logo and our information on the site needs to be updated.

We are changing our hosting site to Nimbrashost.example ,also wanting to start a blog which is linked to the club, plus we wish to sell a small exclusive range of Velmo linked merchandise which will also be available on Tradeva.

I have attached a pdf of the majority of the content. additionally we will provide pictures and a videoclip which should be able to be viewed by pc's, lap tops and mobile phones (the whole website must be fully accessible via phone).

The new site must be able to be updated by someone with medium computer knowledge (usually me), by no means expert. Updates will generally be new pictures and written information. The site must be able to be transferred to NimbrasHost.

Velmo is one of the countries leading clubs and emphasises friendliness, fun & safety for its members, we look after you to ensure your experience is the best we can offer. We are very proud of our reputation, built up over more than 10 years.

Target Market(s)

Swingers, dreamers & fantasists, alternative lifestyle people

Coding

Coded - Design and coding required

Number of Pages Required

5+ page

Font styles to use
Sans Serif

Colors
000000
ec1f27
fbfbfb
eeeeee
eaeaea

Requirements
Must have
• website with blog attached, link to tradeva & quidlo, ability to run videoclip and picture album and must be compatable to transfer easily to Nimbrashost and be updated by non-professional (who can learn)
• Straightforward & easy to navigate
• over 18 content page with enter button
Nice to have
• sexy site
• link to chirpster maybe
• black site would be nice with red or white writing
Should not have
• children and animals in anyway shape or form

```html
<!DOCTYPE html>
<html lang="en">
<head>
<meta charset="utf-8">
<title>Velmo – Swingers Club</title>
<link href="https://fonts.googleapis.com/css2?family=Cinzel:wght@400;700&family=Open+Sans:wght@400;600;700&display=swap" rel="stylesheet">
<style>
:root{
  --black:#000000;
  --red:#ec1f27;
  --white:#ffffff;
  --off:#fbfbfb;
  --light:#eeeeee;
  --muted:#bcbcbc;
  --panel:#161616;
  --dark:#0b0b0b;
}
*{box-sizing:border-box;margin:0;padding:0}
html,body{width:1200px;height:3315px;overflow:hidden;background:var(--black)}
body{position:relative;font-family:"Open Sans",Arial,sans-serif;color:var(--white)}
.section{position:absolute;left:0;width:1200px}
.serif{font-family:"Cinzel",Georgia,serif;font-weight:400}
.btn{display:inline-block;font-size:12px;font-weight:700;text-transform:uppercase;letter-spacing:.5px;text-align:center}
.btn-outline{border:2px solid var(--white);color:var(--white);padding:11px 20px;border-radius:3px}
.btn-red{background:var(--red);color:var(--white);padding:12px 28px;border-radius:2px}

/* hero */
.hero{top:0;height:530px;background:linear-gradient(180deg,#2a2c33 0%,#3b3a3c 35%,#4a3b2e 70%,#1c1b1c 100%)}
.hero-scene{position:absolute;inset:0}
.topbar{position:absolute;right:100px;top:16px;font-size:13px;color:var(--light);display:flex;gap:10px;align-items:center}
.topbar .ico{color:var(--red)}
.brand{position:absolute;left:98px;top:34px;font-family:"Cinzel",Georgia,serif;font-size:38px;color:var(--white);letter-spacing:1px}
.nav{position:absolute;right:95px;top:56px;display:flex;gap:17px;font-size:14px;color:var(--white)}
.nav .active{color:var(--red)}
.hero-title{position:absolute;top:160px;width:100%;text-align:center;font-family:"Cinzel",Georgia,serif;font-size:80px;letter-spacing:18px}
.hero-tag{position:absolute;top:260px;width:100%;text-align:center;font-size:21px;font-weight:600;line-height:36px}
.hero-btn{position:absolute;top:354px;left:511px}
.dots{position:absolute;top:470px;left:564px;display:flex;gap:7px}
.dots span{width:11px;height:11px;border:2px solid var(--white);border-radius:50%}
.dots span.on{background:var(--white)}

/* welcome */
.welcome{top:530px;height:520px;background:var(--red)}
.welcome-frame{position:absolute;left:30px;top:30px;width:1140px;height:455px;border:2px solid rgba(255,255,255,.75)}
.welcome h2{position:absolute;top:80px;width:100%;text-align:center;font-size:34px}
.welcome p{position:absolute;top:150px;left:200px;width:800px;text-align:center;font-size:13px;line-height:30px}
.feature{position:absolute;top:240px;width:260px;text-align:center}
.feature .ring{width:146px;height:146px;border:2px solid var(--white);border-radius:50%;margin:0 auto;display:flex;align-items:center;justify-content:center}
.feature h3{margin-top:30px;font-size:18px;letter-spacing:.5px}

/* about */
.about{top:1050px;height:515px;background:linear-gradient(180deg,#2a1612,#3a2018 50%,#1d0f0c)}
.about-photo{position:absolute;left:98px;top:67px;width:405px;height:383px;border:4px solid var(--off);background:linear-gradient(135deg,#7a1d3a,#c43a5e 45%,#2a0d14)}
.about h2{position:absolute;left:560px;top:60px;font-size:36px;line-height:50px}
.about-text{position:absolute;left:560px;top:186px;width:545px;font-size:13px;line-height:26px;color:var(--light)}
.about-text p{margin-bottom:18px}
.about .btn{position:absolute;left:560px;top:413px}

/* news cards */
.news{top:1565px;height:540px;background:var(--black)}
.card{position:absolute;top:65px;width:314px;height:395px;background:var(--panel);text-align:center}
.card .pic{height:180px}
.card h3{margin-top:26px;font-size:20px;line-height:31px;color:var(--red)}
.card p{margin:14px 26px 0;font-size:12.5px;line-height:23px;color:var(--light);height:80px;overflow:hidden}
.card .btn{margin-top:20px}

/* blog */
.blog{top:2105px;height:410px;background:linear-gradient(180deg,#2b1212,#3a1b17 60%,#1f0d0b)}
.blog h2{position:absolute;top:62px;width:100%;text-align:center;font-size:36px}
.post{position:absolute;top:155px;width:470px;height:182px}
.post .thumb{position:absolute;left:0;top:0;width:190px;height:180px;border:3px solid var(--off)}
.post .body{position:absolute;left:218px;top:0;width:250px}
.post h3{font-size:16px;line-height:26px}
.post .meta{font-size:11px;margin-top:8px;color:var(--light)}
.post .meta b{color:var(--red)}
.post p{font-size:11.5px;line-height:20px;margin-top:10px;color:var(--light)}
.post .more{display:block;margin-top:14px;font-size:11px;font-weight:700;color:var(--red)}

/* products */
.products{top:2515px;height:530px;background:linear-gradient(180deg,#1f1f1f,#2e2e2e 50%,#151515)}
.products h2{position:absolute;top:62px;width:100%;text-align:center;font-size:36px}
.product{position:absolute;top:140px;width:237px}
.product .shot{height:226px;background:var(--off);display:flex;align-items:center;justify-content:center}
.product .shot div{width:150px;height:170px;border-radius:6px}
.product p{margin-top:20px;font-size:14px;line-height:22px;color:var(--light)}
.product .row{display:flex;justify-content:space-between;align-items:center;margin-top:10px}
.product .price{color:var(--red);font-weight:700;font-size:17px}
.product .store{font-weight:700;font-size:16px;color:var(--white)}
.arrow{position:absolute;top:235px;width:38px;height:38px;border:2px solid var(--white);border-radius:50%;display:flex;align-items:center;justify-content:center}

/* footer */
.footer{top:3045px;height:270px;background:var(--black);border-top:5px solid var(--red)}
.contact{position:absolute;top:55px;display:flex;align-items:center;gap:14px;font-size:14px}
.contact .ico{width:44px;height:44px;border:2px solid var(--white);border-radius:50%;display:flex;align-items:center;justify-content:center;flex:none}
.foot-nav{position:absolute;top:140px;width:100%;display:flex;justify-content:center;gap:16px;font-size:14px;font-weight:600}
.foot-rule{position:absolute;top:185px;left:98px;width:1004px;border-top:1px solid #333}
.copy{position:absolute;top:220px;left:98px;font-size:12px;color:var(--light)}
.social{position:absolute;top:205px;right:98px;display:flex;gap:10px}
.social span{width:38px;height:38px;border:2px solid var(--white);border-radius:50%}
</style>
</head>
<body>

<section class="section hero">
  <div class="hero-scene" role="img" aria-label="Night city skyline with lit towers"></div>
  <div class="topbar"><span class="ico">&#9742;</span><span>0700 555 0142</span><span>|</span><span class="ico">&#9993;</span><span>velmoswingers@example.co.uk</span></div>
  <div class="brand">VELMO</div>
  <nav class="nav">
    <span class="active">Home</span><span>Diary</span><span>Theme Parties</span><span>TV/TG and Admirers</span><span>Membership</span><span>FAQs</span><span>Rooms</span><span>Contact Us</span><span>Links</span>
    <svg width="15" height="15" viewBox="0 0 16 16" aria-label="Search"><circle cx="6.5" cy="6.5" r="5" fill="none" stroke="#fff" stroke-width="2.2"/><line x1="10.2" y1="10.2" x2="15" y2="15" stroke="#fff" stroke-width="2.4"/></svg>
  </nav>
  <h1 class="hero-title">VELMO</h1>
  <p class="hero-tag">We are a Swingers Club in the UK Velmo is one of the countries leading clubs<br>and emphasises friendliness, fun &amp; safety for its members.</p>
  <span class="btn btn-outline hero-btn">Get More Info</span>
  <div class="dots"><span class="on"></span><span></span><span></span><span></span></div>
</section>

<section class="section welcome">
  <div class="welcome-frame"></div>
  <h2 class="serif">Welcome to Velmo</h2>
  <p>We are the best in the North East, and have recently been voted No 2 club in the UK. We have retained the coveted title of No 1 friendliest club in the UK (in joint 1st place with our great friends "Night Orchard", London).</p>
  <div class="feature" style="left:92px">
    <div class="ring"><svg width="60" height="64" viewBox="0 0 60 64"><path d="M4 6h52L33 32v22h11v6H16v-6h11V32z" fill="#fff"/></svg></div>
    <h3 class="serif">Leading Clubs</h3>
  </div>
  <div class="feature" style="left:470px">
    <div class="ring"><svg width="72" height="56" viewBox="0 0 72 56"><circle cx="36" cy="13" r="10" fill="#fff"/><circle cx="14" cy="19" r="8" fill="#fff"/><circle cx="58" cy="19" r="8" fill="#fff"/><path d="M20 54c0-16 7-26 16-26s16 10 16 26z" fill="#fff"/><path d="M0 50c0-12 6-20 14-20 4 0 7 2 9 5-3 5-5 10-5 15z" fill="#fff"/><path d="M72 50c0-12-6-20-14-20-4 0-7 2-9 5 3 5 5 10 5 15z" fill="#fff"/></svg></div>
    <h3 class="serif">Emphasises Friendliness</h3>
  </div>
  <div class="feature" style="left:847px">
    <div class="ring"><svg width="62" height="62" viewBox="0 0 62 62"><circle cx="31" cy="31" r="27" fill="none" stroke="#fff" stroke-width="4"/><path d="M18 32l9 9 17-19" fill="none" stroke="#fff" stroke-width="5" stroke-linecap="round" stroke-linejoin="round"/></svg></div>
    <h3 class="serif">Fun &amp; Safety</h3>
  </div>
</section>

<section class="section about">
  <div class="about-photo" role="img" aria-label="Club play room lit in red and pink"></div>
  <h2 class="serif">Velmo :: A Great<br>Place To Meet And Play!</h2>
  <div class="about-text">
    <p>We are the best Swingers Club in the North East, and also voted No 2 club in the UK.</p>
    <p>We have retained the coveted title of No 1 friendliest club in the UK (in joint 1st place with our great friends "Night Orchard", London). This prestigious award has been given to us by a panel of "mystery voters" (swingers, singles &amp; couples) working with the publication called "Late Night Guide" a copy of which is available in reception. Please see our Frequently Asked Questions and Membership pages for more information about the club and its facilities. Velmo was established in Sunderland in 2004 by Alex.</p>
  </div>
  <span class="btn btn-outline">Read More</span>
</section>

<section class="section news">
  <article class="card" style="left:98px">
    <div class="pic" role="img" aria-label="Dark red room with a wooden wheel feature" style="background:linear-gradient(135deg,#6a1a0c,#c0391a 50%,#3a0e06)"></div>
    <h3 class="serif">Price Increases<br>(From April 2017)</h3>
    <p>It is with regret that we have to increase some of our charges, this is due, in the main, to increased running costs</p>
    <span class="btn btn-red">Read More</span>
  </article>
  <article class="card" style="left:443px">
    <div class="pic" role="img" aria-label="Glasses raised in a toast at a party" style="background:linear-gradient(135deg,#2c3a66,#c79a5a 50%,#5a1a22)"></div>
    <h3 class="serif">Membership<br>Fees</h3>
    <p>New members (Couples and Single guys) - (annual) £30, this now includes the next 2 visits half price.</p>
    <span class="btn btn-red">Read More</span>
  </article>
  <article class="card" style="left:788px">
    <div class="pic" role="img" aria-label="Warmly lit bedroom suite" style="background:linear-gradient(135deg,#3a2a18,#b0704a 50%,#2a1a12)"></div>
    <h3 class="serif">Membership<br>Discounts</h3>
    <p>We discount entry and membership to support Her Majesty's Forces (serving and retired), we are now happy to extend</p>
    <span class="btn btn-red">Read More</span>
  </article>
</section>

<section class="section blog">
  <h2 class="serif">Our Blog</h2>
  <article class="post" style="left:98px">
    <div class="thumb" role="img" aria-label="Hotel style room with television" style="background:linear-gradient(135deg,#4a3a2a,#9a7a5a 50%,#2a2018)"></div>
    <div class="body">
      <h3 class="serif">At vero eos et accusamus et iusto odio dignipra</h3>
      <div class="meta"><b>&#9636;</b> 17/06/2017 &nbsp;|&nbsp; <b>&#9679;</b> Alex</div>
      <p>Nam libero tempore, cum soluta nobis elindi optio cumque nihil impedo</p>
      <span class="more">READ MORE &gt;&gt;</span>
    </div>
  </article>
  <article class="post" style="left:630px">
    <div class="thumb" role="img" aria-label="Bedroom with dark headboard" style="background:linear-gradient(135deg,#2a2e3a,#8a8aa0 50%,#1a1a22)"></div>
    <div class="body">
      <h3 class="serif">At vero eos et accusamus et iusto odio dignipra</h3>
      <div class="meta"><b>&#9636;</b> 17/06/2017 &nbsp;|&nbsp; <b>&#9679;</b> Alex</div>
      <p>Nam libero tempore, cum soluta nobis elindi optio cumque nihil impedo</p>
      <span class="more">READ MORE &gt;&gt;</span>
    </div>
  </article>
</section>

<section class="section products">
  <h2 class="serif">Velmo Products</h2>
  <div class="arrow" style="left:38px"><svg width="12" height="14" viewBox="0 0 12 14"><path d="M9 1L3 7l6 6" fill="none" stroke="#fff" stroke-width="2.4"/></svg></div>
  <div class="arrow" style="left:1124px"><svg width="12" height="14" viewBox="0 0 12 14"><path d="M3 1l6 6-6 6" fill="none" stroke="#fff" stroke-width="2.4"/></svg></div>
  <div class="product" style="left:98px">
    <div class="shot"><div role="img" aria-label="Black branded t-shirt" style="background:linear-gradient(180deg,#222,#000)"></div></div>
    <p>At vero eos et accusamus eiuto odio dignissimos duc.</p>
    <div class="row"><span class="price">$20.00</span><span class="store">tradeva</span></div>
  </div>
  <div class="product" style="left:354px">
    <div class="shot"><div role="img" aria-label="Red branded mug" style="background:linear-gradient(180deg,#f0323a,#b5141b)"></div></div>
    <p>At vero eos et accusamus eiuto odio dignissimos duc.</p>
    <div class="row"><span class="price">$20.00</span><span class="store">tradeva</span></div>
  </div>
  <div class="product" style="left:610px">
    <div class="shot"><div role="img" aria-label="Branded wine bottle" style="width:50px;background:linear-gradient(180deg,#3a0a10,#120204)"></div></div>
    <p>At vero eos et accusamus eiuto odio dignissimos duc.</p>
    <div class="row"><span class="price">$20.00</span><span class="store">tradeva</span></div>
  </div>
  <div class="product" style="left:865px">
    <div class="shot"><div role="img" aria-label="Red branded cap" style="height:120px;background:linear-gradient(180deg,#f0323a,#b5141b)"></div></div>
    <p>At vero eos et accusamus eiuto odio dignissimos duc.</p>
    <div class="row"><span class="price">$20.00</span><span class="store">tradeva</span></div>
  </div>
</section>

<footer class="section footer">
  <div class="contact" style="left:180px">
    <span class="ico"><svg width="14" height="20" viewBox="0 0 14 20"><path d="M7 0a7 7 0 0 0-7 7c0 5 7 13 7 13s7-8 7-13a7 7 0 0 0-7-7z" fill="#fff"/><circle cx="7" cy="7" r="2.6" fill="#000"/></svg></span>
    <span>12 Harbour Row, 3rd Floor<br>Tynecastle</span>
  </div>
  <div class="contact" style="left:500px">
    <span class="ico"><svg width="18" height="18" viewBox="0 0 18 18"><path d="M4 1l3 4-2 2c1 2 4 5 6 6l2-2 4 3-2 3C8 17 1 10 1 4z" fill="#fff"/></svg></span>
    <span>0700 555 0142</span>
  </div>
  <div class="contact" style="left:725px">
    <span class="ico"><svg width="20" height="14" viewBox="0 0 20 14"><rect x="1" y="1" width="18" height="12" fill="none" stroke="#fff" stroke-width="2"/><path d="M1 1l9 7 9-7" fill="none" stroke="#fff" stroke-width="2"/></svg></span>
    <span>velmoswingers@example.co.uk</span>
  </div>
  <nav class="foot-nav"><span>HOME</span><span>DIARY</span><span>THEME PARTIES</span><span>TV/TG AND ADMIRERS</span><span>MEMBERSHIP</span><span>FAQS</span><span>ROOMS</span><span>CONTACT US</span><span>LINKS</span></nav>
  <div class="foot-rule"></div>
  <p class="copy">Copyrights © 2017, Velmo. All rights reserved.</p>
  <div class="social" aria-label="Social links"><span></span><span></span><span></span></div>
</footer>

</body>
</html>
```